Residential improvers, A Quiet Harbor 9 Z *

Quiet Harbor 9 Z is a real estate company specializing in turning unloved properties into improved, happy places to live. We specialize in thoughtfully-improved residential properties for buyers or renters. Our company needs a business card that reflects the renovated homes we create using green and Feng Shui principles,

Please disregard the images we submitted. We are looking for an abstract, sophisticated elegant design. No eggs in a nest ... nothing cute. The image can be soft.
Updates

Aloha (hello) all designers. We are a serious property investment/improvement company. We strive to be unique, renovating with style and elegance. Our business card must portray the same message. We thought the nest and flower might be "it" ... clearly it's not, once we saw what you submitted. Please revisit the brief as it was modified yesterday. Mahalo for your input! We look forward to hearing from all designers that have been invited.

Industry/Entity Type

Real Estate Development

Contact Information for Business Card

We will have separate business cards for
1) Corabeth Dunmore 555-310-7290 corabeth@mailvista.test
2) Tessa Harwick 555-347-6152 tessaharwick@mailvista.test
** can we add the website later ... in the process of approval.
Investors * Renovators * Connectors

Font styles to use
Sans Serif

Colors
cadf82

Requirements
Must have
• a feng shui feel ... modern. Color - green with black print.
Nice to have
• A Quiet Harbor 9 Z

```html
<!DOCTYPE html>
<html lang="en">
<head>
<meta charset="utf-8">
<title>A Quiet Harbor 9 Z – Business Card</title>
<link href="https://fonts.googleapis.com/css2?family=Montserrat:wght@400;500;600;700&display=swap" rel="stylesheet">
<style>
  :root {
    --green: #cadf82;
    --ink: #1c1c1c;
    --paper: #ffffff;
    --backdrop: #d9dadc;
  }
  * { margin: 0; padding: 0; box-sizing: border-box; }
  html, body {
    width: 1200px; height: 880px; overflow: hidden;
    background: var(--backdrop);
    font-family: "Montserrat", sans-serif;
  }
  .stage { position: relative; width: 1200px; height: 880px; }
  .card {
    position: absolute; width: 560px; height: 320px;
    background: var(--paper); border-radius: 16px; overflow: hidden;
    box-shadow: 0 10px 30px rgba(0,0,0,.18);
  }
  .card--front { left: 90px; top: 70px; }
  .card--back { left: 550px; top: 480px; }

  .brand {
    position: absolute; display: flex; align-items: center; gap: 12px;
    color: var(--ink); font-weight: 600; white-space: nowrap;
  }
  .brand__dot {
    width: 18px; height: 18px; border-radius: 50%; background: var(--green); flex: none;
  }
  .card--front .brand { left: 50%; top: 50%; transform: translate(-50%, -50%); font-size: 30px; }
  .card--back .brand { left: 34px; top: 116px; font-size: 24px; }

  .card__art { position: absolute; inset: 0; }

  .tagline {
    position: absolute; right: 24px; top: 20px; list-style: none;
    text-align: right; font-size: 12px; font-weight: 500; color: var(--ink); line-height: 1.45;
  }
  .tagline li::after {
    content: ""; display: inline-block; width: 7px; height: 7px; margin-left: 6px;
    border-radius: 50%; background: var(--green); vertical-align: middle;
  }

  .contact {
    position: absolute; right: 22px; top: 178px; text-align: right; color: var(--paper);
    white-space: nowrap;
  }
  .contact__name { font-size: 15px; font-weight: 700; margin-bottom: 8px; letter-spacing: .2px; }
  .contact__list { list-style: none; font-size: 11.5px; font-weight: 500; line-height: 1; }
  .contact__list li { display: flex; justify-content: flex-end; align-items: center; gap: 8px; margin-bottom: 6px; height: 18px; }
  .contact__icon { width: 18px; height: 18px; flex: none; }
</style>
</head>
<body>
<main class="stage">

  <section class="card card--front" aria-label="Card front">
    <div class="brand"><span class="brand__dot"></span>A Quiet Harbor 9 Z</div>
  </section>

  <section class="card card--back" aria-label="Card back">
    <svg class="card__art" viewBox="0 0 560 320" width="560" height="320" aria-hidden="true">
      <path d="M100 320 C200 300 280 265 300 170 C295 265 230 310 160 320 Z" fill="var(--green)"/>
      <path d="M215 320 C265 300 300 262 318 200 C340 115 410 78 560 70 L560 78 C420 86 356 120 336 200 C318 268 280 304 235 320 Z" fill="var(--ink)"/>
      <path d="M250 320 C300 300 330 260 345 200 C365 120 430 95 560 88 L560 320 Z" fill="var(--ink)"/>
    </svg>

    <div class="brand"><span class="brand__dot"></span>A Quiet Harbor 9 Z</div>

    <ul class="tagline">
      <li>Investors</li>
      <li>Renovators</li>
      <li>Connectors</li>
    </ul>

    <div class="contact">
      <p class="contact__name">Corabeth Dunmore</p>
      <ul class="contact__list">
        <li>555-310-7290
          <svg class="contact__icon" viewBox="0 0 18 18"><circle cx="9" cy="9" r="8" fill="none" stroke="var(--green)" stroke-width="1.5"/><rect x="6.5" y="4.5" width="5" height="9" rx="1" fill="none" stroke="var(--green)" stroke-width="1.2"/></svg>
        </li>
        <li>corabeth@mailvista.test
          <svg class="contact__icon" viewBox="0 0 18 18"><circle cx="9" cy="9" r="8" fill="none" stroke="var(--green)" stroke-width="1.5"/><rect x="5" y="6" width="8" height="6" fill="none" stroke="var(--green)" stroke-width="1.2"/><path d="M5 6 L9 9.5 L13 6" fill="none" stroke="var(--green)" stroke-width="1.2"/></svg>
        </li>
        <li>www.quietharbor.test
          <svg class="contact__icon" viewBox="0 0 18 18"><circle cx="9" cy="9" r="8" fill="none" stroke="var(--green)" stroke-width="1.5"/><circle cx="9" cy="9" r="4.5" fill="none" stroke="var(--green)" stroke-width="1.1"/><path d="M4.5 9 H13.5 M9 4.5 V13.5" stroke="var(--green)" stroke-width="1.1"/></svg>
        </li>
      </ul>
    </div>
  </section>

</main>
</body>
</html>
```